Kelvaro.ch is looking for business card letterhead and envelope C5 with WOW effect

We need a strong business card for our company Kelvaro.ch, logo is available. You want a black or dark background on which the logo Stark r% 26 # 252; appears. Letterhead and envelope in C5 format should be in a similar design, but does not have to be We need a strong business card for our company Kelvaro.ch, logo is available. A black or dark background is desired, on which the logo Stark comes across. The letterhead and the envelope in C5 format should have a similar design.

Target Market(s)

Private customers as well as entrepreneurs

Contact Information for Business Card

E-mail: info@kelvaro-example.ch
Web.www.Kelvaro-example.ch
Tel: +41 ( 0 ) 79 482 6037
Adresse:
Lindenweg 14
9406 Tarnbach

Hier kann man Icons verwenden für Email,Tel und Adressse

Font styles to use
Other font styles liked:
• Dubai,bold

Colors

Designer to choose colors to be used in the design.

Requirements
Must have
• WOW effect
Nice to have
• R% 26 # 252; back business card with our service listings. - VEHICLE LABELING - SHOP WINDOW LABELING - STICKERS AND MUCH MORE ... in red color

```html
<!DOCTYPE html>
<html lang="en">
<head>
<meta charset="utf-8">
<title>Kelvaro.ch Business Card</title>
<link rel="stylesheet" href="https://fonts.googleapis.com/css2?family=Roboto:wght@300;400;500;700&display=swap">
<style>
  :root {
    --stage: #2a2a2c;
    --card: #1f1f20;
    --accent: #f5c518;
    --ink: #e9e9e9;
    --muted: #bdbdbd;
    --emboss: #3a3a3c;
    --rule: #8a8a8a;
  }
  * { box-sizing: border-box; margin: 0; padding: 0; }
  html, body { width: 1200px; height: 880px; overflow: hidden; }
  body {
    background: var(--stage);
    font-family: "Roboto", Arial, sans-serif;
    position: relative;
  }
  .card {
    position: absolute;
    left: 290px;
    width: 620px;
    height: 354px;
    background: var(--card);
    border-radius: 18px;
    overflow: hidden;
    border-bottom: 7px solid var(--accent);
  }
  .card--back { top: 68px; }
  .card--front { top: 458px; }

  /* Back side: services */
  .back-brand {
    position: absolute;
    top: 72px; left: 0; right: 0;
    text-align: center;
    font-weight: 700;
    font-size: 44px;
    letter-spacing: 2px;
    color: var(--emboss);
    text-transform: uppercase;
  }
  .services {
    position: absolute;
    top: 190px; left: 0; right: 0;
    text-align: center;
  }
  .services__title {
    color: var(--accent);
    font-weight: 500;
    font-size: 30px;
    margin-bottom: 14px;
  }
  .services__list {
    color: var(--ink);
    font-weight: 300;
    font-size: 17px;
    line-height: 1.45;
    text-transform: uppercase;
  }
  .services__dot {
    display: inline-block;
    width: 9px; height: 9px;
    border-radius: 50%;
    background: var(--accent);
    margin: 0 6px 2px;
  }

  /* Front side: contact */
  .brand {
    position: absolute;
    left: 62px; top: 150px;
    display: flex; align-items: center; gap: 14px;
  }
  .brand__mark {
    width: 40px; height: 40px;
    background: var(--accent);
  }
  .brand__name {
    color: var(--ink);
    font-weight: 700;
    font-size: 30px;
    letter-spacing: 1px;
    text-transform: uppercase;
  }
  .divider {
    position: absolute;
    left: 352px; top: 92px;
    width: 1px; height: 160px;
    background: var(--rule);
  }
  .contact {
    position: absolute;
    left: 378px; top: 86px;
    color: var(--ink);
  }
  .contact__name {
    color: var(--accent);
    font-weight: 500;
    font-size: 25px;
  }
  .contact__role {
    font-weight: 300;
    font-size: 15px;
    color: var(--muted);
    margin: 2px 0 14px 14px;
  }
  .contact__row {
    display: flex; align-items: flex-start; gap: 10px;
    font-weight: 300;
    font-size: 15px;
    line-height: 1.3;
    margin-bottom: 8px;
  }
  .contact__row svg { flex: none; margin-top: 2px; }
  .contact__lines { display: flex; flex-direction: column; }
  .contact__web em { font-style: normal; color: var(--accent); }
</style>
</head>
<body>
  <section class="card card--back">
    <div class="back-brand">Kelvaro.ch</div>
    <div class="services">
      <h2 class="services__title">our service listings</h2>
      <p class="services__list">Vehicle labeling<span class="services__dot"></span>Shop window labeling<br>Stickers and much more</p>
    </div>
  </section>

  <section class="card card--front">
    <div class="brand">
      <span class="brand__mark"></span>
      <span class="brand__name">Kelvaro.ch</span>
    </div>
    <div class="divider"></div>
    <div class="contact">
      <h1 class="contact__name">Mareike Odermatt</h1>
      <p class="contact__role">Manager</p>
      <div class="contact__row">
        <svg width="14" height="18" viewBox="0 0 14 18"><path d="M7 0C3.1 0 0 3.1 0 7c0 5 7 11 7 11s7-6 7-11c0-3.9-3.1-7-7-7zm0 9.5A2.5 2.5 0 1 1 7 4.5a2.5 2.5 0 0 1 0 5z" fill="var(--accent)"/></svg>
        <div class="contact__lines"><span>Lindenweg 14</span><span>9406 Tarnbach</span></div>
      </div>
      <div class="contact__row">
        <svg width="14" height="14" viewBox="0 0 24 24"><path d="M6.6 10.8a15 15 0 0 0 6.6 6.6l2.2-2.2c.3-.3.7-.4 1-.2 1.1.4 2.3.6 3.6.6.6 0 1 .4 1 1V20c0 .6-.4 1-1 1A17 17 0 0 1 3 4c0-.6.4-1 1-1h3.5c.6 0 1 .4 1 1 0 1.3.2 2.5.6 3.6.1.3 0 .7-.2 1z" fill="var(--accent)"/></svg>
        <span>+41 ( 0 ) 79 482 6037</span>
      </div>
      <div class="contact__row">
        <svg width="14" height="14" viewBox="0 0 24 24"><path d="M2 5h20v14H2z" fill="var(--accent)"/><path d="M2 5l10 8 10-8" fill="none" stroke="var(--card)" stroke-width="2"/></svg>
        <span>info@kelvaro-example.ch</span>
      </div>
      <div class="contact__row">
        <svg width="14" height="14" viewBox="0 0 24 24"><circle cx="12" cy="12" r="10" fill="var(--accent)"/><path d="M2 12h20M12 2c3 3 3 17 0 20M12 2c-3 3-3 17 0 20" fill="none" stroke="var(--card)" stroke-width="1.5"/></svg>
        <span class="contact__web">www.<em>Kelvaro-example</em>.ch</span>
      </div>
    </div>
  </section>
</body>
</html>
```